Healthcare/Medical Consultant Company

QRN is a Healthcare Conultant Company. We help doctors manage the business side of their medical practice.
We already have a very basic world press design. We want an upgraded design that conveys partnership, healthcare expertise and healthcare innovation to our client. It needs to have a sleek, clean, modern and inclusive look. Pictures need need to convey diversity (including pictures of people of all races and shows both men and women working together in a healthcare environment to make it better). The Pictures on the home page should particularly illustrate diversity and Healthcare expertise. The company logo is blue and white but the site doesn’t have to follow the exact same theme but the logo needs to blend well with the chosen theme. The logo should ideally be in the header of the website. We would also like the following included in our website:

1. Pages should include: a home page, About Us page, Services page, Get a quote page, Contact Us page, Staff page(where we can add pictures and bio for staff).

2. The Drop down menu for services should have hyperlinks ( for each service)Leading to a page that provides detailed info about that specific service. Our services include: Revenue Cycle Management, Regulatory Compliance, Human Resources Management, & practice Management.

3. Links to social media should in the header or footer of each page.

4. Contact info should be in the footer of each page.

5. Clients should be an email to us from the contact page.

Target Market(s)

Physician Medical Practices

Industry/Entity Type

Medical

Coding

Coded - Design and coding required

Font styles to use
Sans Serif

Colors

Designer to choose colors to be used in the design.

Requirements
Must have
• See project description
Nice to have
• See project description

```html
<!DOCTYPE html>
<html lang="en">
<head>
<meta charset="utf-8">
<title>QRN – Quarnel Health Allies</title>
<link href="https://fonts.googleapis.com/css2?family=Lato:wght@400;700&family=Raleway:wght@300;400;600;700&display=swap" rel="stylesheet">
<style>
:root{
  --blue:#1f6fc1;
  --blue-dark:#0b4a9c;
  --blue-deep:#063a86;
  --sky:#3aa0dc;
  --sky-light:#2e95d8;
  --ink:#3a3a3a;
  --muted:#777;
  --line:#e3e6ea;
  --white:#fff;
  --bg:#fff;
}
*{box-sizing:border-box;margin:0;padding:0}
html,body{width:1200px;height:4018px;overflow:hidden;background:var(--bg)}
body{position:relative;font-family:'Lato',sans-serif;color:var(--ink)}
.abs{position:absolute}
.section-title{position:absolute;left:0;width:1200px;text-align:center;font-family:'Raleway',sans-serif;font-weight:400;font-size:38px;color:var(--sky)}
.section-title b{font-weight:700;color:var(--blue-dark)}

/* hero */
.hero{position:absolute;left:0;top:0;width:1200px;height:650px;overflow:hidden}
.hero-photo{position:absolute;inset:0;background:linear-gradient(120deg,#8c9aa6 0%,#c9d2d8 35%,#e9ecee 55%,#aab4bc 80%,#7d8893 100%)}
.hero-shade{position:absolute;left:0;top:0;width:1200px;height:120px;background:rgba(20,30,45,.55)}
.logo{position:absolute;left:80px;top:22px;width:200px;text-align:center;color:var(--white);font-family:'Lato',sans-serif}
.logo-name{font-size:44px;font-weight:700;line-height:1}
.logo-sub{font-size:13px;font-weight:400;margin-top:6px;letter-spacing:.5px}
.nav{position:absolute;left:383px;top:54px;display:flex;gap:36px;font-family:'Raleway',sans-serif;font-size:16px;font-weight:600;color:var(--white)}
.nav .active{position:relative}
.nav .active::after{content:"";position:absolute;left:50%;top:54px;margin-left:-12px;border:12px solid transparent;border-bottom-color:var(--white);border-top:0}
.social{position:absolute;display:flex;gap:32px}
.social span{width:42px;height:42px;border-radius:50%;background:var(--white);display:block}
.hero-title{position:absolute;left:0;width:1200px;text-align:center;color:var(--white)}
.hero-mark{top:270px;font-family:'Raleway',sans-serif;font-weight:700;font-size:84px;color:var(--sky-light);line-height:1}
.hero-name{top:360px;font-family:'Raleway',sans-serif;font-weight:600;font-size:50px}
.hero-text{top:420px;left:250px;width:700px;font-size:17px;font-weight:700;font-style:italic;line-height:27px}
.dots{position:absolute;top:584px;left:553px;display:flex;gap:14px}
.dots span{width:20px;height:20px;border-radius:50%;border:2px solid var(--white)}
.dots .on{background:var(--white);box-shadow:inset 0 0 0 4px rgba(60,70,80,.8)}

/* welcome */
.welcome-kicker{position:absolute;top:735px;left:0;width:1200px;text-align:center;font-family:'Raleway',sans-serif;font-weight:300;font-size:34px;color:var(--sky)}
.welcome-name{position:absolute;top:776px;left:0;width:1200px;text-align:center;font-family:'Raleway',sans-serif;font-weight:700;font-size:36px;color:var(--blue-dark)}
.welcome-text{position:absolute;top:840px;left:262px;width:676px;text-align:center;font-size:15px;line-height:25px;color:var(--muted)}
.down{position:absolute;top:998px;left:572px;width:56px;height:56px;border-radius:50%;background:var(--white);box-shadow:0 2px 8px rgba(0,0,0,.2)}

/* services */
.services-band{position:absolute;left:0;top:1196px;width:1200px;height:590px}
.service{position:absolute;color:var(--white);width:360px}
.service h3{font-family:'Raleway',sans-serif;font-weight:600;font-size:22px;margin-bottom:10px}
.service p{font-size:14px;line-height:24px}
.service.left{text-align:right}

/* team */
.team-card{position:absolute;top:1921px;width:336px;height:544px;border:1px solid var(--line);background:var(--white)}
.team-photo{position:absolute;left:0;top:0;width:334px;height:250px}
.team-tag{position:absolute;left:24px;top:222px;width:286px;height:76px;background:var(--white);box-shadow:0 3px 8px rgba(0,0,0,.18);text-align:center}
.team-tag h4{font-family:'Raleway',sans-serif;font-weight:600;font-size:20px;color:var(--ink);margin-top:13px}
.team-tag p{font-size:14px;color:var(--sky);margin-top:6px}
.hours{position:absolute;left:12px;top:320px;width:310px;font-size:13px;color:var(--muted)}
.hours .row{display:flex;justify-content:space-between;height:44px;align-items:center;border-bottom:1px solid var(--line)}
.hours .row:last-child{border-bottom:0}
.hours b{color:var(--ink);font-weight:700}
.btn{position:absolute;background:var(--sky-light);color:var(--white);font-family:'Raleway',sans-serif;font-weight:700;font-size:16px;text-align:center;text-transform:uppercase}
.team-card .btn{left:88px;top:466px;width:158px;height:50px;line-height:50px}

/* cta */
.cta-head{position:absolute;left:654px;top:2640px;width:460px;font-family:'Raleway',sans-serif;font-weight:700;font-size:38px;line-height:46px;color:var(--white)}
.cta-text{position:absolute;left:654px;top:2752px;width:480px;font-size:18px;line-height:32px;font-weight:700;font-style:italic;color:var(--white)}
.cta-btn{position:absolute;left:654px;top:2880px;width:136px;height:56px;line-height:56px;background:var(--blue-deep);color:var(--white);font-family:'Raleway',sans-serif;font-weight:700;font-size:15px;text-align:center}

/* contact */
.info{position:absolute;top:3172px;display:flex;gap:16px;align-items:flex-start}
.info-icon{width:62px;height:62px;border-radius:50%;background:var(--blue-dark);flex:none}
.info small{display:block;font-size:14px;color:var(--muted);margin-top:6px}
.info strong{display:block;font-size:17px;font-weight:700;color:var(--ink);margin-top:4px;line-height:24px}
.field{position:absolute;left:118px;width:472px;height:62px;border:1px solid var(--line);box-shadow:0 1px 4px rgba(0,0,0,.08);padding:20px 16px;font-size:14px;color:var(--muted)}
.field.message{left:611px;width:470px;height:311px}
.submit{left:522px;top:3633px;width:156px;height:54px;line-height:54px}

/* footer */
.footer{position:absolute;left:0;top:3688px;width:1200px;height:330px}
.footer-links{position:absolute;top:3892px;left:0;width:1200px;display:flex;justify-content:center;gap:26px;font-family:'Raleway',sans-serif;font-size:19px;color:var(--white)}
.copyright{position:absolute;top:3944px;left:0;width:1200px;text-align:center;font-size:13px;color:var(--white)}
</style>
</head>
<body>

<!-- Hero -->
<header class="hero">
  <div class="hero-photo" role="img" aria-label="Doctor and colleague reviewing patient files in a bright clinic office"></div>
  <div class="hero-shade"></div>
  <svg class="abs" style="left:0;top:0" width="1200" height="650">
    <polygon points="0,628 600,590 1200,610 1200,650 0,650" fill="#ffffff"/>
    <polygon points="0,622 600,572 1200,605 1200,618 600,594 0,640" fill="var(--sky-light)"/>
  </svg>
  <div class="logo"><div class="logo-name">QRN</div><div class="logo-sub">Quarnel Health Allies LLC</div></div>
  <nav class="nav">
    <span class="active">HOME</span><span>ABOUT US</span><span>SERVICES</span><span>GET A QUOTE</span><span>CONTACT US</span>
  </nav>
  <div class="social" style="left:973px;top:46px"><span></span><span></span><span></span></div>
  <div class="hero-title hero-mark">QRN</div>
  <div class="hero-title hero-name">Quarnel Health Allies</div>
  <p class="hero-title hero-text">Lorem Ipsum is simply dummy text of the printing and typesetting industry. Lorem Ipsum has been the industry's standard dummy text ever since the 1500s.</p>
  <div class="dots"><span></span><span class="on"></span><span></span></div>
</header>

<!-- Welcome -->
<section>
  <div class="welcome-kicker">Welcome to</div>
  <h1 class="welcome-name">QRN Quarnel Health Allies</h1>
  <p class="welcome-text">Lorem Ipsum is simply dummy text of the printing and typesetting industry. Lorem Ipsum has been the industry's standard dummy text ever since the 1500s, when an unknown printer took a galley of type and scrambled it to make a type specimen book. It has survived not only five centuries, but also the leap into electronic typesetting, remaining essentially unchanged. It was popularised in the 1960s with the release of Letraset sheets containing.</p>
  <div class="down"><svg width="56" height="56"><path d="M28 18v20M21 31l7 7 7-7" stroke="var(--blue-dark)" stroke-width="2.5" fill="none"/></svg></div>
</section>

<!-- Services -->
<section>
  <h2 class="section-title" style="top:1104px">Our <b>SERVICES</b></h2>
  <svg class="services-band" width="1200" height="590" role="img" aria-label="Medical team meeting in a clinic, tinted blue">
    <defs>
      <linearGradient id="svcGrad" x1="0" y1="0" x2="1" y2="1">
        <stop offset="0" stop-color="#2a6db8"/><stop offset=".5" stop-color="#3d7fc6"/><stop offset="1" stop-color="#1c5aa8"/>
      </linearGradient>
    </defs>
    <polygon points="0,4 590,50 590,586 0,520" fill="url(#svcGrad)"/>
    <polygon points="610,50 1200,0 1200,520 610,586" fill="url(#svcGrad)"/>
    <line x1="600" y1="46" x2="600" y2="590" stroke="#fff" stroke-width="3"/>
    <g fill="#fff" stroke="#3aa0dc" stroke-width="3">
      <circle cx="600" cy="140" r="9"/><circle cx="600" cy="220" r="9"/><circle cx="600" cy="305" r="9"/><circle cx="600" cy="390" r="9"/><circle cx="600" cy="470" r="9"/>
    </g>
    <g>
      <line x1="556" y1="79" x2="592" y2="79" stroke="#fff" stroke-width="2"/>
      <line x1="556" y1="245" x2="592" y2="245" stroke="#fff" stroke-width="2"/>
      <line x1="556" y1="411" x2="592" y2="411" stroke="#fff" stroke-width="2"/>
      <line x1="608" y1="162" x2="640" y2="162" stroke="#fff" stroke-width="2"/>
      <line x1="608" y1="328" x2="640" y2="328" stroke="#fff" stroke-width="2"/>
    </g>
    <g fill="#fff">
      <circle cx="509" cy="79" r="48"/><circle cx="509" cy="245" r="48"/><circle cx="509" cy="411" r="48"/>
      <circle cx="686" cy="162" r="48"/><circle cx="686" cy="328" r="48"/>
    </g>
    <g fill="var(--blue-dark)">
      <circle cx="509" cy="79" r="38"/><circle cx="509" cy="245" r="38"/><circle cx="509" cy="411" r="38"/>
      <circle cx="686" cy="162" r="38"/><circle cx="686" cy="328" r="38"/>
    </g>
    <g fill="none" stroke="#fff" stroke-width="3">
      <circle cx="509" cy="79" r="18"/><path d="M499 79h20M509 69v20"/>
      <rect x="494" y="232" width="18" height="26"/><circle cx="522" cy="240" r="6"/><path d="M512 258q10-12 20 0"/>
      <circle cx="509" cy="401" r="7"/><path d="M493 428q16-22 32 0"/>
      <rect x="672" y="146" width="26" height="32"/><path d="M685 156v12M679 162h12"/>
      <rect x="668" y="312" width="36" height="22"/><path d="M676 326v4M684 320v10M692 316v14"/>
    </g>
  </svg>
  <div class="service left" style="left:74px;top:1262px"><h3>Revenue Cycle Management</h3><p>Lorem Ipsum is simply dummy text of the<br>printing and typesetting industry.</p></div>
  <div class="service left" style="left:74px;top:1428px"><h3>Regulatory Compliance</h3><p>Lorem Ipsum is simply dummy text of the<br>printing and typesetting industry.</p></div>
  <div class="service left" style="left:74px;top:1594px"><h3>Staff Education and Training</h3><p>Lorem Ipsum is simply dummy text of the<br>printing and typesetting industry.</p></div>
  <div class="service" style="left:769px;top:1345px"><h3>Medical Billing &amp; Coding</h3><p>Lorem Ipsum is simply dummy text of the<br>printing and typesetting industry.</p></div>
  <div class="service" style="left:769px;top:1511px"><h3>Human Resources Training</h3><p>Lorem Ipsum is simply dummy text of the<br>printing and typesetting industry.</p></div>
</section>

<!-- Team -->
<section>
  <h2 class="section-title" style="top:1840px"><span style="font-weight:400">Meet</span> <b>OUR TEAM</b></h2>

  <article class="team-card" style="left:78px">
    <div class="team-photo" role="img" aria-label="Portrait of a health advisor in front of a brick wall" style="background:linear-gradient(135deg,#9a4e3a,#c47a5c 50%,#7f3c2c)"></div>
    <div class="team-tag"><h4>DANA MOREL</h4><p>Health Advisor</p></div>
    <div class="hours">
      <div class="row"><span>Monday - Wednesday</span><b>18:00 - 7:00</b></div>
      <div class="row"><span>Friday</span><b>14:30 - 9:00</b></div>
      <div class="row"><span>Saturday</span><b>8:00 - 14:00</b></div>
    </div>
    <div class="btn">View Profile</div>
  </article>

  <article class="team-card" style="left:434px">
    <div class="team-photo" role="img" aria-label="Portrait of a health advisor holding a folder" style="background:linear-gradient(135deg,#6f7780,#a9b2ba 50%,#5e6871)"></div>
    <div class="team-tag"><h4>DANA MOREL</h4><p>Health Advisor</p></div>
    <div class="hours">
      <div class="row"><span>Monday - Wednesday</span><b>18:00 - 7:00</b></div>
      <div class="row"><span>Friday</span><b>14:30 - 9:00</b></div>
      <div class="row"><span>Saturday</span><b>8:00 - 14:00</b></div>
    </div>
    <div class="btn">View Profile</div>
  </article>

  <article class="team-card" style="left:788px">
    <div class="team-photo" role="img" aria-label="Portrait of a health advisor in a suit" style="background:linear-gradient(135deg,#dfe3e7,#b8c2cc 50%,#8f99a4)"></div>
    <div class="team-tag"><h4>DANA MOREL</h4><p>Health Advisor</p></div>
    <div class="hours">
      <div class="row"><span>Monday - Wednesday</span><b>18:00 - 7:00</b></div>
      <div class="row"><span>Friday</span><b>14:30 - 9:00</b></div>
      <div class="row"><span>Saturday</span><b>8:00 - 14:00</b></div>
    </div>
    <div class="btn">View Profile</div>
  </article>
</section>

<!-- Call to action -->
<section>
  <svg class="abs" style="left:0;top:2518px" width="1200" height="506">
    <defs>
      <linearGradient id="ctaGrad" x1="0" y1="0" x2="1" y2="0">
        <stop offset="0" stop-color="#3aa0dc"/><stop offset="1" stop-color="#0b4a9c"/>
      </linearGradient>
      <linearGradient id="ctaPhoto" x1="0" y1="0" x2="1" y2="1">
        <stop offset="0" stop-color="#cfd6dc"/><stop offset=".5" stop-color="#9aa7b3"/><stop offset="1" stop-color="#5d6b79"/>
      </linearGradient>
    </defs>
    <polygon points="0,14 600,56 600,506 0,464" fill="url(#ctaPhoto)" role="img" aria-label="Two healthcare professionals reviewing notes together"/>
    <polygon points="600,56 1200,0 1200,450 600,506" fill="url(#ctaGrad)"/>
  </svg>
  <h2 class="cta-head">PROVIDE TOTAL HEALTH CARE SOLUTION</h2>
  <p class="cta-text">Lorem Ipsum is simply dummy text of the printing and typesetting industry. Lorem Ipsum has been the industry's standard dummy text ever since the 1500s.</p>
  <div class="cta-btn">GET A QUOTE</div>
</section>

<!-- Contact -->
<section>
  <h2 class="section-title" style="top:3084px"><span style="font-weight:400">Contact</span> <b>US</b></h2>

  <div class="info" style="left:108px">
    <svg class="info-icon" viewBox="0 0 62 62"><path d="M22 18c3 0 5 5 5 7s-3 3-2 5 5 6 7 7 3-2 5-2 7 2 7 5-4 5-7 5c-10 0-22-12-22-22 0-3 4-5 7-5z" fill="#fff"/></svg>
    <div><small>Call us Now</small><strong>(555) 210-4471</strong></div>
  </div>
  <div class="info" style="left:414px">
    <svg class="info-icon" viewBox="0 0 62 62"><path d="M31 14a11 11 0 0 1 11 11c0 9-11 22-11 22S20 34 20 25a11 11 0 0 1 11-11z" fill="#fff"/><circle cx="31" cy="25" r="4" fill="var(--blue-dark)"/></svg>
    <div><small>Location</small><strong>118 Harbor Lane Suite 310<br>Brookfield, NY 10990</strong></div>
  </div>
  <div class="info" style="left:767px">
    <svg class="info-icon" viewBox="0 0 62 62"><rect x="17" y="21" width="28" height="20" rx="2" fill="#fff"/><path d="M17 22l14 11 14-11" stroke="var(--blue-dark)" stroke-width="2" fill="none"/></svg>
    <div><small>Email Us</small><strong>info@quarnelhealth.com</strong></div>
  </div>

  <div class="field" style="top:3290px">Name :</div>
  <div class="field" style="top:3373px">Email :</div>
  <div class="field" style="top:3456px">Phone :</div>
  <div class="field" style="top:3539px">Subject :</div>
  <div class="field message" style="top:3290px">Message / Comments :</div>
  <div class="btn submit">Submit Now</div>
</section>

<!-- Footer -->
<footer>
  <svg class="footer" width="1200" height="330">
    <defs>
      <linearGradient id="footGrad" x1="0" y1="0" x2="0" y2="1">
        <stop offset="0" stop-color="#0b4a9c"/><stop offset="1" stop-color="#1f6fc1"/>
      </linearGradient>
    </defs>
    <polygon points="0,0 1200,40 1200,330 0,330" fill="url(#footGrad)"/>
  </svg>
  <div class="social" style="left:528px;top:3818px;gap:16px"><span></span><span></span><span></span></div>
  <nav class="footer-links"><span>Home</span><span>|</span><span>About</span><span>|</span><span>Services</span><span>|</span><span>Get A Quote</span><span>|</span><span>Contact</span></nav>
  <p class="copyright">Copyright © QRN QUARNEL HEALTH ALLIES - 2018 . All Right Reserved</p>
</footer>

</body>
</html>
```